Professional Package for CPA Firm

We would like a stationery design for our new CPA Firm based in Atlanta, GA called 'Vale 8'. We work with investors to help grow investments, tax free. We would like the design to have a professional/minimal look with a 'wow' factor. We need 9.5″ x 4.125″, 9x12, and 10x13 mailing envelopes, business cards, and a letterhead. We have a logo that is already complete. For the letterhead, we would like to have space to put credentials at the bottom of the page

Industry/Entity Type

CPA, Accounting

```html
<!DOCTYPE html>
<html lang="en">
<head>
<meta charset="utf-8">
<title>Vale 8 — Stationery Set</title>
<link href="https://fonts.googleapis.com/css2?family=Montserrat:wght@400;800&family=Open+Sans:wght@400;600&family=Roboto:wght@400&display=swap" rel="stylesheet">
<style>
  :root {
    --bg: #e8e8e8;
    --paper: #f3f3f3;
    --ink: #1b1b1b;
    --body-ink: #4a4a4a;
    --brand-blue: #2a97cf;
    --charcoal: #1a1a1a;
    --card-back: #333333;
    --shadow: 0 2px 6px rgba(0,0,0,0.18);
  }
  * { margin: 0; padding: 0; box-sizing: border-box; }
  html, body { width: 1200px; height: 795px; overflow: hidden; }
  body {
    background: radial-gradient(ellipse at 50% 40%, #f2f2f2 0%, var(--bg) 100%);
    position: relative;
    font-family: "Open Sans", sans-serif;
    color: var(--body-ink);
  }
  .sheet { position: absolute; background: var(--paper); box-shadow: var(--shadow); }

  /* Wordmark */
  .wordmark { display: flex; flex-direction: column; align-items: center; }
  .wordmark-name {
    font-family: "Montserrat", sans-serif; font-weight: 800; color: var(--ink);
    display: flex; align-items: center; line-height: 1; letter-spacing: 0.5px;
  }
  .wordmark-dot { background: var(--brand-blue); display: inline-block; margin-right: 0.3em; width: 0.55em; height: 0.55em; }
  .wordmark-tagline { font-family: "Montserrat", sans-serif; font-weight: 400; color: var(--ink); letter-spacing: 0.6px; margin-top: 2px; }

  /* Letterhead */
  .letterhead { left: 292px; top: 99px; width: 294px; height: 415px; }
  .letterhead .wordmark { position: absolute; top: 58px; left: 0; right: 0; }
  .letterhead .wordmark-name { font-size: 16px; }
  .letterhead .wordmark-tagline { font-size: 5px; }
  .letter-body { position: absolute; left: 26px; top: 98px; width: 241px; font-size: 5.3px; line-height: 8px; }
  .letter-body p { margin-bottom: 8px; text-align: justify; }
  .letter-footer { position: absolute; left: 0; right: 0; top: 380px; text-align: center; font-family: "Roboto", sans-serif; font-size: 5.8px; line-height: 8.5px; color: #555; }
  .letter-footer svg { width: 5px; height: 5px; vertical-align: -0.5px; margin: 0 1px 0 4px; fill: #333; }

  /* Folder */
  .folder { left: 636px; top: 80px; width: 347px; height: 437px; }
  .folder-spine { position: absolute; left: 4px; top: 0; bottom: 0; width: 14px; border-left: 1px solid #d6d6d6; border-right: 1px solid #d6d6d6; }
  .folder .wordmark { position: absolute; top: 80px; left: 0; right: 0; }
  .folder .wordmark-name { font-size: 22px; }
  .folder .wordmark-tagline { font-size: 6.5px; }
  .folder-photo { position: absolute; left: 0; top: 143px; width: 347px; height: 226px; }
  .folder-url { position: absolute; left: 0; right: 0; top: 396px; text-align: center; font-family: "Montserrat", sans-serif; font-size: 9.5px; letter-spacing: 1.6px; color: #444; }
  .folder-url span { color: var(--brand-blue); }

  /* Business cards */
  .card-front { left: 187px; top: 550px; width: 133px; height: 75px; }
  .card-front .wordmark { position: absolute; left: 10px; top: 28px; width: 48px; }
  .card-front .wordmark-name { font-size: 8.5px; }
  .card-front .wordmark-tagline { font-size: 2.6px; margin-top: 1px; letter-spacing: 0.2px; }
  .card-divider { position: absolute; left: 63px; top: 21px; width: 1px; height: 35px; background: var(--brand-blue); }
  .card-details { position: absolute; left: 70px; top: 21px; font-family: "Roboto", sans-serif; font-size: 3.1px; line-height: 4.2px; color: #333; }
  .card-name { font-family: "Open Sans", sans-serif; font-weight: 600; font-size: 4px; color: var(--ink); line-height: 4.5px; }
  .card-role { margin-bottom: 2px; }
  .card-back { left: 187px; top: 647px; width: 133px; height: 75px; background: var(--card-back); }

  /* Envelopes */
  .envelope-front { left: 353px; top: 561px; width: 329px; height: 157px; }
  .envelope-front .return { position: absolute; left: 22px; top: 50px; width: 70px; text-align: center; }
  .envelope-front .wordmark-name { font-size: 13px; }
  .envelope-front .wordmark-tagline { font-size: 4px; }
  .envelope-front .return-address { font-family: "Roboto", sans-serif; font-size: 5.5px; line-height: 7px; color: #444; margin-top: 3px; }
  .envelope-back { left: 714px; top: 561px; width: 328px; height: 157px; }
  .envelope-flap { position: absolute; left: 0; top: 0; width: 328px; height: 52px; }
  .envelope-back .wordmark { position: absolute; left: 0; right: 0; top: 20px; }
  .envelope-back .wordmark-name { font-size: 9px; color: #ffffff; }
  .envelope-back .wordmark-tagline { font-size: 2.8px; color: #ffffff; margin-top: 1px; }
</style>
</head>
<body>

<!-- Letterhead -->
<section class="sheet letterhead">
  <div class="wordmark">
    <div class="wordmark-name"><span class="wordmark-dot"></span>VALE 8</div>
    <div class="wordmark-tagline">CPAs and Tax Advisors</div>
  </div>
  <div class="letter-body">
    <p>Dear customer,</p>
    <p>Lorem ipsum dolor sit amet, consectetur adipisicing elit, sed do eiusmod tempor incididunt ut labore et dolore magna aliqua. Ut enim ad minim veniam, quis nostrud exercitation ullamco laboris nisi ut aliquip ex ea commodo consequat. Duis aute irure dolor in reprehenderit in voluptate velit esse cillum dolore eu fugiat nulla pariatur. Excepteur sint occaecat cupidatat non proident, sunt in culpa qui officia deserunt mollit anim id est laborum.</p>
    <p>Lorem ipsum dolor sit amet, consectetur adipisicing elit, sed do eiusmod tempor incididunt ut labore et dolore magna aliqua. Ut enim ad minim veniam, quis nostrud exercitation ullamco laboris nisi ut aliquip ex ea commodo consequat. Duis aute irure dolor in reprehenderit in voluptate velit esse cillum dolore eu fugiat nulla pariatur. Excepteur sint occaecat cupidatat non proident, sunt in culpa qui officia deserunt mollit anim id est laborum.</p>
    <p>Lorem ipsum dolor sit amet, consectetur adipisicing elit, sed do eiusmod tempor incididunt ut labore et dolore magna aliqua. Ut enim ad minim veniam, quis nostrud exercitation ullamco laboris nisi ut aliquip ex ea commodo consequat. Duis aute irure dolor in reprehenderit in voluptate velit esse cillum dolore eu fugiat nulla pariatur. Excepteur sint occaecat cupidatat non proident, sunt in culpa qui officia deserunt mollit anim id est laborum.</p>
    <p>Lorem ipsum dolor sit amet, consectetur adipisicing elit, sed do eiusmod tempor incididunt ut labore et dolore magna aliqua. Ut enim ad minim veniam, quis nostrud exercitation ullamco laboris nisi ut aliquip ex ea commodo consequat. Duis aute irure dolor in reprehenderit.</p>
    <p>Yours Sincerely,</p>
  </div>
  <div class="letter-footer">
    48 Harbor Ridge Lane, Marietta, GA 30060<br>
    <svg viewBox="0 0 10 10"><path d="M2 0.5 L3.8 0.5 L4.5 3 L3.2 4 Q4.2 6 6 6.8 L7 5.5 L9.5 6.2 L9.5 8 Q9.5 9.5 8 9.5 Q1 9 0.5 2 Q0.5 0.5 2 0.5Z"/></svg>+14045550187
    <svg viewBox="0 0 10 10"><rect x="0.5" y="2" width="9" height="6.5"/><path d="M0.5 2 L5 6 L9.5 2" stroke="#f3f3f3" stroke-width="1" fill="none"/></svg>info@valeeight.com
    <svg viewBox="0 0 10 10"><circle cx="5" cy="5" r="4.3" fill="none" stroke="#333" stroke-width="1"/><path d="M0.7 5 H9.3 M5 0.7 V9.3" stroke="#333" stroke-width="0.8"/></svg>www.valeeight.com
  </div>
</section>

<!-- Presentation folder -->
<section class="sheet folder">
  <div class="folder-spine"></div>
  <div class="wordmark">
    <div class="wordmark-name"><span class="wordmark-dot"></span>VALE 8</div>
    <div class="wordmark-tagline">CPAs and Tax Advisors</div>
  </div>
  <svg class="folder-photo" viewBox="0 0 347 226" role="img" aria-label="Photograph of two colleagues working together at a laptop in a bright office">
    <defs>
      <linearGradient id="officeTones" x1="0" y1="0" x2="1" y2="1">
        <stop offset="0" stop-color="#b88a66"/>
        <stop offset="0.45" stop-color="#d9d4cf"/>
        <stop offset="1" stop-color="#4a4f58"/>
      </linearGradient>
    </defs>
    <rect width="347" height="226" fill="url(#officeTones)"/>
    <polygon points="0,14 92,226 0,226" fill="#3a3a3a" opacity="0.8"/>
    <polygon points="252,2 347,2 347,226" fill="var(--brand-blue)" opacity="0.85"/>
  </svg>
  <div class="folder-url">www.<span>valeeight</span>.com</div>
</section>

<!-- Business card, front -->
<section class="sheet card-front">
  <div class="wordmark">
    <div class="wordmark-name"><span class="wordmark-dot"></span>VALE 8</div>
    <div class="wordmark-tagline">CPAs and Tax Advisors</div>
  </div>
  <div class="card-divider"></div>
  <div class="card-details">
    <div class="card-name">MARCUS ELLERY</div>
    <div class="card-role">Managing Director</div>
    <div>48 Harbor Ridge Lane,</div>
    <div>Marietta, GA 30060</div>
    <div>+14045550187</div>
    <div>info@valeeight.com</div>
    <div>www.valeeight.com</div>
  </div>
</section>

<!-- Business card, back -->
<section class="sheet card-back" role="img" aria-label="Dark charcoal card back with a repeating brand pattern"></section>

<!-- Envelope, front -->
<section class="sheet envelope-front">
  <div class="return">
    <div class="wordmark">
      <div class="wordmark-name"><span class="wordmark-dot"></span>VALE 8</div>
      <div class="wordmark-tagline">CPAs and Tax Advisors</div>
    </div>
    <div class="return-address">48 Harbor Ridge Lane,<br>Marietta, GA 30060</div>
  </div>
</section>

<!-- Envelope, back -->
<section class="sheet envelope-back">
  <svg class="envelope-flap" viewBox="0 0 328 52">
    <polygon points="0,0 328,0 322,50 6,50" fill="var(--charcoal)"/>
  </svg>
  <div class="wordmark">
    <div class="wordmark-name"><span class="wordmark-dot"></span>VALE 8</div>
    <div class="wordmark-tagline">CPAs and Tax Advisors</div>
  </div>
</section>

</body>
</html>
```